Business Card Design

Hi I need a business card designed, we already have the business name logo artwork and would like some concept ideas for the Bus Card layout.
On the back of the card i want to include the products and services that we offer.
We are a Plastics Sheeting manufacture based in Perth Australia.

                                       

We need a BC design for a company called Tarvo Plastics based in Perth Australia.

We supply from DIY to Trade & Industrial  Engineering Markets.

We specialise in:

·         Cut to size panels  (all shapes and sizes)

·         Plastics fabrication & Welding

·         Custom Designs

·         Plastic Repairs

·         PVC Pipe Slotting & PVC Pipe Threading

·         Supplier of all types of engineering plastics and profiles.

Including:           Acrylic / Clarvene

                               Polycarbonate / Dorvil

                               Prismatic Light Diffuser

                               Vantrib

                               HDPE / UHMWPE

                               PVC / PVC Foam

                               Nylon

                               HIPS

```html
<!DOCTYPE html>
<html lang="en">
<head>
<meta charset="utf-8">
<title>Tarvo Plastics – Business Card</title>
<link rel="stylesheet" href="https://fonts.googleapis.com/css2?family=Source+Sans+3:wght@400;600;700&display=swap">
<style>
  :root {
    --navy: #1f3b70;
    --orange: #f0871d;
    --text-grey: #4f5459;
    --rule-grey: #9aa0a6;
    --silver-light: #f1f2f3;
    --silver-mid: #dcdee1;
    --silver-dark: #c6c9cd;
    --page-bg: #e9eaec;
    --white: #ffffff;
  }
  * { box-sizing: border-box; margin: 0; padding: 0; }
  html, body {
    width: 1200px; height: 720px; overflow: hidden;
    background: var(--page-bg);
    font-family: "Source Sans 3", "Segoe UI", Arial, sans-serif;
  }
  .canvas {
    width: 1200px; height: 720px;
    display: flex; align-items: center; justify-content: center; gap: 40px;
  }
  .card {
    position: relative;
    width: 560px; height: 320px;
    background: linear-gradient(120deg, var(--silver-light) 0%, var(--white) 30%, var(--silver-mid) 65%, var(--silver-dark) 100%);
    box-shadow: 0 6px 18px rgba(0,0,0,0.18);
    overflow: hidden;
  }
  .brand {
    display: flex; align-items: center; gap: 10px;
    color: var(--navy); font-weight: 700; letter-spacing: -0.5px;
    line-height: 1;
  }
  .brand-mark {
    width: 14px; height: 14px; background: var(--orange); flex: none;
  }

  /* Front */
  .card-front .brand { position: absolute; left: 40px; top: 42px; font-size: 52px; }
  .person { position: absolute; left: 40px; top: 140px; }
  .person-name { font-size: 17px; font-weight: 700; color: var(--navy); }
  .person-title { color: var(--orange); font-weight: 600; }
  .contact-list { list-style: none; margin-top: 8px; }
  .contact-list li {
    display: flex; align-items: center; gap: 8px;
    font-size: 13px; color: var(--text-grey); line-height: 20px;
  }
  .contact-icon { width: 12px; height: 12px; fill: var(--navy); flex: none; }
  .street-address {
    position: absolute; left: 40px; top: 263px;
    font-size: 13px; color: var(--text-grey);
  }
  .info-band {
    position: absolute; left: 0; bottom: 0; width: 100%; height: 28px;
    background: var(--orange);
  }
  .info-band-postal {
    position: absolute; left: 40px; top: 0; line-height: 28px;
    font-size: 12.5px; color: var(--white); font-weight: 600;
  }
  .info-band-legal {
    position: absolute; right: 0; top: 0; height: 28px; width: 270px;
    background: var(--navy);
    clip-path: polygon(16px 0, 100% 0, 100% 100%, 0 100%);
    color: var(--white); font-size: 11.5px; font-weight: 600;
    line-height: 28px; padding-left: 26px; white-space: nowrap;
  }

  /* Back */
  .card-back .brand { position: absolute; left: 0; right: 0; top: 26px; justify-content: center; font-size: 46px; }
  .offer-heading {
    position: absolute; left: 0; right: 0; top: 90px;
    text-align: center; color: var(--navy);
    font-size: 14px; font-weight: 700; line-height: 18px;
  }
  .offer-columns {
    position: absolute; left: 32px; right: 28px; top: 140px;
    display: flex;
  }
  .offer-column h2 {
    font-size: 16px; font-weight: 700; color: var(--navy); margin-bottom: 4px;
  }
  .offer-column ul { list-style: none; }
  .offer-column li {
    position: relative; padding-left: 12px;
    font-size: 12.5px; line-height: 16px; color: var(--text-grey);
  }
  .offer-column li::before,
  .material-pair span::before {
    content: ""; position: absolute; left: 0; top: 6px;
    width: 5px; height: 5px; border-radius: 50%; background: var(--orange);
  }
  .services { width: 300px; padding-right: 16px; }
  .materials {
    flex: 1; padding-left: 22px;
    border-left: 1px solid var(--rule-grey);
  }
  .material-pair { padding-left: 0 !important; }
  .material-pair::before { display: none; }
  .material-pair span { position: relative; padding-left: 12px; margin-right: 10px; }
</style>
</head>
<body>
<main class="canvas">

  <section class="card card-front" aria-label="Business card front">
    <div class="brand"><span class="brand-mark"></span>Tarvo Plastics</div>

    <div class="person">
      <p class="person-name">Your Name, <span class="person-title">Title</span></p>
      <ul class="contact-list">
        <li>
          <svg class="contact-icon" viewBox="0 0 24 24" aria-hidden="true"><path d="M6.6 10.8a15.1 15.1 0 0 0 6.6 6.6l2.2-2.2c.3-.3.7-.4 1-.2 1.1.4 2.3.6 3.6.6.6 0 1 .4 1 1V20c0 .6-.4 1-1 1C10.6 21 3 13.4 3 4c0-.6.4-1 1-1h3.5c.6 0 1 .4 1 1 0 1.3.2 2.5.6 3.6.1.3 0 .7-.2 1z"/></svg>
          08 5550 2011
        </li>
        <li>
          <svg class="contact-icon" viewBox="0 0 24 24" aria-hidden="true"><path d="M7 1h10a2 2 0 0 1 2 2v18a2 2 0 0 1-2 2H7a2 2 0 0 1-2-2V3a2 2 0 0 1 2-2zm0 4v13h10V5zm5 14.5a1.2 1.2 0 1 0 0 2.4 1.2 1.2 0 0 0 0-2.4z"/></svg>
          0400 555 789
        </li>
        <li>
          <svg class="contact-icon" viewBox="0 0 24 24" aria-hidden="true"><path d="M6 2h12v6H6zM4 9h16a2 2 0 0 1 2 2v7h-4v4H6v-4H2v-7a2 2 0 0 1 2-2zm4 8v3h8v-3z"/></svg>
          08 5550 2022
        </li>
        <li>
          <svg class="contact-icon" viewBox="0 0 24 24" aria-hidden="true"><path d="M2 5h20v14H2zm2 2v.5l8 5 8-5V7l-8 5z"/></svg>
          sales@tarvoplastics.com.au
        </li>
      </ul>
    </div>

    <p class="street-address">Unit 4/18 Kestrel Circuit Tallowin WA 6155</p>

    <div class="info-band">
      <span class="info-band-postal">PO Box 2240 Tallowin DC WA 6970</span>
      <span class="info-band-legal">Orvel Holdings Pty Ltd T/A Tarvo Plastics ABN: TBA</span>
    </div>
  </section>

  <section class="card card-back" aria-label="Business card back">
    <div class="brand"><span class="brand-mark"></span>Tarvo Plastics</div>

    <p class="offer-heading">The Products And Services That We Offer<br>Are Supplied From Diy To Trade &amp; Industrial Engineering Markets</p>

    <div class="offer-columns">
      <div class="offer-column services">
        <h2>We specialise in:</h2>
        <ul>
          <li>Cut to size panels (all shapes and sizes)</li>
          <li>Plastics fabrication &amp; Welding</li>
          <li>Custom Designs</li>
          <li>Plastic Repairs</li>
          <li>PVC Pipe Slotting &amp; PVC Pipe Threading</li>
          <li>Supplier of all types of engineering plastics and profiles</li>
        </ul>
      </div>
      <div class="offer-column materials">
        <h2>Including:</h2>
        <ul>
          <li>Acrylic / Clarvene</li>
          <li>Polycarbonate / Dorvil</li>
          <li>Prismatic Light Diffuser</li>
          <li class="material-pair"><span>Vantrib</span><span>HDPE / UHMWPE</span></li>
          <li>PVC / PVC Foam</li>
          <li class="material-pair"><span>Nylon</span><span>HIPS</span></li>
        </ul>
      </div>
    </div>
  </section>

</main>
</body>
</html>
```